Web design for financial services

A modern web design of financial services (brokerage firm)
Req.s and technology tags :
- Very mobile friendly.
- One paged with some inner pages.
- Animated sticky header .
- Member login area for e-trade.
- Support RTL language.
- HTML & CSS.

The logo will be Home link
• MPTR :
WHO WE ARE
Content :
i) Board of Directors
ii) Mission Statement
iii) Corporate Values
iv) Regulations
• Financial Services :
WHAT WE DO
Content:
i) Electronic trading
ii) Trading desk
iii) Institutional
iv) Investors Education
• News
• Market Tools
• Forms---- opens new page
• Careers---- opens new page
• Contact Us----opens new page

The website is :
http://www.mptr-doha-example.com/

The logo need some changes to be more modern and impressively , but with keeping same structure .

Some related websites :
https://www.lv-bourse.example/

financial market

Financial Service

Coded - Design and coding required

2 page

• same fonts of http://www.kwdholdings.example/

• - Very mobile friendly.
• - One paged with some inner pages.
• - Animated sticky header .
• - Member login area for e-trade.
• - Support RTL language.
• - HTML & CSS.
• Slider , some Qatari theme,
• i like the video inside the home page
• ex :http://www.kwdholdings.example/

```html
<!DOCTYPE html>
<html lang="en">
<head>
<meta charset="utf-8">
<title>MPTR – Brokers At Lusail Bourse</title>
<link rel="stylesheet" href="https://fonts.googleapis.com/css2?family=Roboto:wght@300;400;500;700&family=Quicksand:wght@400;500&display=swap">
<style>
:root{
  --red:#a3231f;
  --red-dark:#7e1714;
  --ink:#333333;
  --muted:#6b6b6b;
  --grey-band:#ececec;
  --light-band:#f4f4f4;
  --white:#ffffff;
  --sky-top:#8fa6b8;
  --sky-bottom:#c9bfae;
}
*{box-sizing:border-box;margin:0;padding:0}
html,body{width:1200px;height:2912px;overflow:hidden}
body{font-family:"Roboto",Arial,sans-serif;color:var(--ink);background:var(--white);position:relative}
section,header,footer{position:absolute;left:0;width:1200px}
.btn{display:inline-block;background:var(--red);color:var(--white);font-size:15px;font-weight:500;padding:12px 26px;border-radius:3px;text-decoration:none}
.section-title{font-weight:400;font-size:46px;text-align:center;color:var(--ink)}
.title-rule{width:620px;height:3px;background:var(--red);margin:14px auto 0}

/* hero */
.hero{top:0;height:440px;overflow:hidden}
.hero-photo{position:absolute;inset:0;background:linear-gradient(180deg,var(--sky-top) 0%,#aab3b7 45%,var(--sky-bottom) 80%,#8a7d6c 100%)}
.hero-shade{position:absolute;inset:0;background:linear-gradient(180deg,rgba(0,0,0,.35) 0%,rgba(0,0,0,.05) 40%,rgba(0,0,0,.2) 100%)}
.brand{position:absolute;left:110px;top:30px;display:flex;align-items:center;gap:12px;color:var(--white);font-size:30px;font-weight:700;letter-spacing:1px}
.brand-mark{width:56px;height:56px;border-radius:50%;background:var(--red);border:3px solid var(--white)}
.utility{position:absolute;right:100px;top:36px;display:flex;gap:26px;font-size:15px;color:var(--white)}
.utility span{display:flex;align-items:center;gap:6px}
.utility .lang{color:#f0c9c7}
.main-nav{position:absolute;right:100px;top:78px;display:flex;gap:28px;font-size:17px;color:var(--white)}
.hero-copy{position:absolute;top:296px;width:100%;text-align:center}
.hero-copy h1{font-family:"Quicksand","Roboto",sans-serif;font-weight:400;font-size:60px;color:var(--white);letter-spacing:.5px}
.hero-copy .btn{margin-top:24px;font-size:16px;padding:13px 24px}
.hero-flag{position:absolute;left:578px;top:290px;width:36px;height:22px;background:var(--red)}

/* welcome */
.welcome{top:440px;height:630px}
.welcome .section-title{margin-top:36px}
.about-intro{position:absolute;left:175px;top:150px;width:400px}
.about-intro h2{font-size:28px;font-weight:500;margin-bottom:20px}
.about-intro p{font-size:13px;line-height:22px;color:var(--muted)}
.about-intro .btn{margin-top:26px;font-size:14px;padding:11px 20px}
.portrait-frame{position:absolute;left:660px;top:110px;width:330px;height:310px;border:3px solid var(--red)}
.portrait{position:absolute;left:620px;top:135px;width:340px;height:255px;background:linear-gradient(135deg,#d8dde2 0%,#b9c2cb 55%,#59606a 100%)}

/* about */
.about{top:1070px;height:330px;background:var(--grey-band)}
.about .section-title{margin-top:72px}
.about p{width:1010px;margin:20px auto 0;font-size:13px;line-height:22px;color:var(--muted);text-align:center}
.about p + p{margin-top:12px}

/* what we do */
.services{top:1400px;height:320px;overflow:hidden}
.services-photo{position:absolute;inset:0;background:linear-gradient(180deg,#4c5660 0%,#6e767c 55%,#5a5248 100%)}
.services-shade{position:absolute;inset:0;background:rgba(20,20,25,.35)}
.services-copy{position:relative;text-align:center;color:var(--white);padding-top:82px}
.services-copy .section-title{color:var(--white)}
.services-copy p{width:980px;margin:16px auto 0;font-size:13px;line-height:21px;color:#e6e6e6}
.services-copy .btn{margin-top:26px;font-size:15px;padding:13px 24px}

/* news */
.news{top:1720px;height:460px}
.news-head{position:absolute;left:95px;top:100px;right:105px;display:flex;justify-content:space-between;align-items:center}
.news-head h2{font-size:44px;font-weight:500;color:var(--red)}
.news-arrows{display:flex;gap:10px}
.news-arrows span{width:30px;height:30px;background:var(--red);display:flex;align-items:center;justify-content:center}
.news-rule{position:absolute;left:95px;right:105px;top:158px;height:1px;background:#dddddd}
.news-grid{position:absolute;left:95px;top:180px;display:flex;gap:80px}
.news-card{width:290px}
.news-image{height:170px}
.news-card h3{font-size:14px;font-weight:400;color:var(--ink);margin-top:14px}
.img-desk{background:linear-gradient(135deg,#d9dde0 0%,#aeb6bb 60%,#7f8a90 100%)}
.img-city{background:linear-gradient(180deg,#b6c6d2 0%,#c8b79c 55%,#8c7a63 100%)}
.img-chart{background:linear-gradient(135deg,#1c4f8a 0%,#3f7fc4 55%,#9cc4ea 100%)}

/* market tools */
.tools{top:2180px;height:380px;background:var(--light-band)}
.tools .section-title{margin-top:46px;font-size:44px}
.tools .title-rule{width:560px;margin-top:14px}
.tool-cols{position:absolute;left:100px;top:150px;display:flex;gap:0}
.tool-col{width:340px;padding-left:0}
.tool-col h3{display:flex;align-items:center;gap:12px;font-size:20px;font-weight:500;color:var(--ink);margin-bottom:18px}
.tool-col li{list-style:none;font-size:13px;color:var(--muted);line-height:30px}

/* footer */
.site-footer{top:2560px;height:352px;background:var(--red);color:var(--white)}
.footer-brand{position:absolute;left:95px;top:42px;width:92px;height:92px;border-radius:50%;border:3px solid var(--white);display:flex;align-items:center;justify-content:center;font-size:22px;font-weight:700}
.footer-col{position:absolute;top:44px}
.footer-col h4{font-size:20px;font-weight:400;margin-bottom:18px}
.contact{left:290px;width:300px}
.contact li{list-style:none;display:flex;gap:12px;font-size:13px;line-height:19px;margin-bottom:14px}
.contact li svg{flex:none;margin-top:2px}
.sitemap{left:640px}
.sitemap li{list-style:none;font-size:13px;line-height:24px}
.newsletter{left:830px;width:280px}
.newsletter p{font-size:12px;color:#f3dcdb;margin-bottom:12px}
.subscribe{display:flex;height:34px}
.subscribe span{flex:1;background:var(--white)}
.subscribe b{width:40px;background:var(--red-dark);display:flex;align-items:center;justify-content:center}
.social{display:flex;gap:22px;margin-top:26px}
.social span{width:22px;height:22px;border-radius:50%;background:var(--white)}
.copyright{position:absolute;left:0;bottom:0;width:100%;height:44px;background:var(--red-dark);font-size:12px;text-align:center;line-height:44px;color:#f3dcdb}
</style>
</head>
<body>

<header class="hero">
  <div class="hero-photo" role="img" aria-label="Doha skyline with glass towers at dusk"></div>
  <div class="hero-shade"></div>
  <div class="brand"><span class="brand-mark"></span>MPTR</div>
  <div class="utility">
    <span><svg width="14" height="14" viewBox="0 0 14 14"><rect x="2" y="6" width="10" height="7" rx="1" fill="#fff"/><path d="M4 6V4a3 3 0 0 1 6 0v2" stroke="#fff" stroke-width="1.5" fill="none"/></svg>Log In</span>
    <span class="lang">EN</span>
  </div>
  <nav class="main-nav">
    <span>MPTR</span><span>Financial Services</span><span>News</span><span>Market Tool</span><span>Forms</span><span>Contact Us</span>
  </nav>
  <div class="hero-flag"></div>
  <div class="hero-copy">
    <h1>Brokers At Lusail Bourse</h1>
    <a class="btn">Learn More &#9654;</a>
  </div>
</header>

<section class="welcome">
  <h2 class="section-title">Welcome To MPTR</h2>
  <div class="title-rule"></div>
  <div class="about-intro">
    <h2>Who We Are</h2>
    <p>MPTR is a private Qatari company that aims to provide secure and technologically advanced methods of trading for its clients. These facilities enable investors to trade faster, more secure and more private, sharing the strategy of our investors with the utmost care and respect.</p>
    <a class="btn">Read More &#9654;</a>
  </div>
  <div class="portrait-frame"></div>
  <div class="portrait" role="img" aria-label="Portrait of a smiling businessman in a suit"></div>
</section>

<section class="about">
  <h2 class="section-title">About MPTR</h2>
  <p>MPTR is a private Qatari company that aims to provide secure and technologically advanced methods of trading to its clients. These facilities enable clients to trade faster, more secure and more private, keeping the strategy of our investors in mind with the utmost care and respect.</p>
  <p>We stand by our clients by offering complete and professional brokerage services, with experienced staff and a modern trading platform. Our team delivers timely market insight, fair execution and clear reporting, together with a strong commitment to every rule set by the local regulator.</p>
</section>

<section class="services">
  <div class="services-photo" role="img" aria-label="Waterfront corniche with birds in flight under a cloudy sky"></div>
  <div class="services-shade"></div>
  <div class="services-copy">
    <h2 class="section-title">What We Do</h2>
    <p>MPTR offers various trading and investment services to its clients, providing secure and technologically advanced methods of trading. These facilities enable clients to trade faster, more secure and more private.</p>
    <a class="btn">Check Out Our Services</a>
  </div>
</section>

<section class="news">
  <div class="news-head">
    <h2>News</h2>
    <div class="news-arrows">
      <span><svg width="10" height="12" viewBox="0 0 10 12"><path d="M8 1 2 6l6 5" stroke="#fff" stroke-width="2" fill="none"/></svg></span>
      <span><svg width="10" height="12" viewBox="0 0 10 12"><path d="m2 1 6 5-6 5" stroke="#fff" stroke-width="2" fill="none"/></svg></span>
    </div>
  </div>
  <div class="news-rule"></div>
  <div class="news-grid">
    <article class="news-card"><div class="news-image img-desk" role="img" aria-label="Desk with financial papers and a pen"></div><h3>Market News - Lusail Bourse</h3></article>
    <article class="news-card"><div class="news-image img-city" role="img" aria-label="Aerial view of a modern Gulf city"></div><h3>Local Economy - Bay Chronicle</h3></article>
    <article class="news-card"><div class="news-image img-chart" role="img" aria-label="Blue financial chart on a screen"></div><h3>Direct Dividend Payment Plan</h3></article>
  </div>
</section>

<section class="tools">
  <h2 class="section-title">Market Tools</h2>
  <div class="title-rule"></div>
  <div class="tool-cols">
    <div class="tool-col">
      <h3><svg width="16" height="20" viewBox="0 0 16 20"><path d="M1 1h14v18l-7-5-7 5z" fill="#333"/></svg>Most Active Company</h3>
      <ul><li>• Lorem Ipsum has been the industry</li><li>• Lorem Ipsum has been the industry</li><li>• Lorem Ipsum has been the industry</li><li>• Lorem Ipsum has been the industry</li></ul>
    </div>
    <div class="tool-col">
      <h3><svg width="20" height="20" viewBox="0 0 20 20"><rect x="1" y="3" width="15" height="15" rx="2" stroke="#333" stroke-width="2" fill="none"/><path d="m5 10 4 4 10-11" stroke="#333" stroke-width="2.2" fill="none"/></svg>Top Gainer</h3>
      <ul><li>• Lorem Ipsum has been the industry</li><li>• Lorem Ipsum has been the industry</li><li>• Lorem Ipsum has been the industry</li><li>• Lorem Ipsum has been the industry</li></ul>
    </div>
    <div class="tool-col">
      <h3><svg width="20" height="20" viewBox="0 0 20 20"><path d="M2 1h4v10H2zM8 1h7l3 8v2h-6l1 6-2 2-3-8z" fill="#333"/></svg>Top Loser</h3>
      <ul><li>• Lorem Ipsum has been the industry</li><li>• Lorem Ipsum has been the industry</li><li>• Lorem Ipsum has been the industry</li><li>• Lorem Ipsum has been the industry</li></ul>
    </div>
  </div>
</section>

<footer class="site-footer">
  <div class="footer-brand">MPTR</div>
  <div class="footer-col contact">
    <h4>Contact Us</h4>
    <ul>
      <li><svg width="14" height="18" viewBox="0 0 14 18"><path d="M7 1a6 6 0 0 1 6 6c0 4-6 10-6 10S1 11 1 7a6 6 0 0 1 6-6z" fill="#fff"/><circle cx="7" cy="7" r="2.2" fill="#a3231f"/></svg>First Floor, Al Noor Tower, West Bay<br>Opposite Harbour Plaza</li>
      <li><svg width="14" height="14" viewBox="0 0 14 14"><path d="M3 1h2l1 3-2 1.5a8 8 0 0 0 4.5 4.5L10 8l3 1v2a2 2 0 0 1-2 2A10 10 0 0 1 1 3a2 2 0 0 1 2-2z" fill="#fff"/></svg>+974 4000 1234</li>
      <li><svg width="16" height="12" viewBox="0 0 16 12"><rect x="0" y="0" width="16" height="12" rx="1" fill="#fff"/><path d="m1 1 7 6 7-6" stroke="#a3231f" stroke-width="1.4" fill="none"/></svg>info@mptr-doha-example.com</li>
    </ul>
  </div>
  <div class="footer-col sitemap">
    <h4>Site Map</h4>
    <ul><li>MPTR</li><li>Financial Services</li><li>News</li><li>Market Tool</li><li>Forms</li><li>Contact Us</li></ul>
  </div>
  <div class="footer-col newsletter">
    <h4>Newsletter</h4>
    <p>Subscribe our latest news, offer and discounts</p>
    <div class="subscribe"><span></span><b><svg width="16" height="14" viewBox="0 0 16 14"><path d="M1 7 15 1l-3 12-4-4-3 3V8z" fill="#fff"/></svg></b></div>
    <div class="social"><span></span><span></span><span></span><span></span></div>
  </div>
  <div class="copyright">Copyright © 2017 MPTR. All Rights Reserved</div>
</footer>

</body>
</html>
```